Heron Loan Partners Business Card

We need a business card design for our mortgage servicing company. In addition to servicing the loans of homeowners, we help homeowners with purchasing their homes and any mortgage refinancing. We would like to see designs that use the colors in the logo attached below (gold-ish yellow and navy blue), and any other design you deem fit! The design should communicate a simpler life with smart mortgages provided by Heron.

```html
<!DOCTYPE html>
<html lang="en">
<head>
<meta charset="utf-8">
<title>Heron Loan Partners Business Card</title>
<link rel="stylesheet" href="https://fonts.googleapis.com/css2?family=Noto+Serif:wght@800&family=Poppins:wght@400;600&display=swap">
<style>
  :root {
    --navy: #231e55;
    --navy-soft: #2b2566;
    --gold: #e3ab34;
    --white: #ffffff;
    --ink: #1a1a1a;
    --rule: #a8a8a8;
    --stage: #e9e9ec;
  }
  * { box-sizing: border-box; margin: 0; padding: 0; }
  html, body { width: 1200px; height: 1108px; overflow: hidden; }
  body {
    background: var(--stage);
    display: flex; align-items: center; justify-content: center; gap: 80px;
    font-family: "Poppins", sans-serif;
  }
  .card {
    width: 400px; height: 680px; border-radius: 28px;
    position: relative; overflow: hidden;
    box-shadow: 0 8px 24px rgba(0,0,0,0.12);
  }
  .card-front { background: var(--white); text-align: center; }
  .card-back { background: var(--navy); display: flex; align-items: center; justify-content: center; }

  .brand-name {
    font-family: "Poppins", sans-serif; font-weight: 600;
    color: var(--gold); font-size: 30px; line-height: 1.1; letter-spacing: 0.5px;
  }
  .card-front .brand { position: absolute; top: 120px; left: 0; right: 0; }
  .card-front .brand-name { color: var(--navy); }

  .holder { position: absolute; top: 360px; left: 0; right: 0; }
  .holder-name {
    font-family: "Noto Serif", serif; font-weight: 800;
    font-size: 34px; color: var(--navy); line-height: 1.1;
  }
  .holder-role {
    font-size: 18px; color: var(--gold); letter-spacing: 1px; margin-top: 2px;
  }

  .icon-row {
    display: flex; align-items: center; justify-content: center; gap: 8px;
    margin: 22px 40px 10px;
  }
  .icon-row .rule { flex: 1; height: 1px; background: var(--rule); }
  .icon {
    width: 30px; height: 30px; border-radius: 6px; background: var(--navy);
    display: flex; align-items: center; justify-content: center;
  }
  .contact-list { list-style: none; font-size: 19px; color: var(--ink); line-height: 1.35; }
  .divider { height: 1px; background: var(--rule); margin: 18px 60px 16px; }
  .address { font-size: 18px; color: var(--ink); line-height: 1.35; font-style: normal; }

  .back-pattern {
    position: absolute; inset: 0;
    background: radial-gradient(circle at 50% 45%, var(--navy-soft), var(--navy) 70%);
  }
  .card-back .brand { position: relative; text-align: center; }
  .card-back .brand-name { font-size: 34px; }
</style>
</head>
<body>
  <article class="card card-front">
    <div class="brand"><p class="brand-name">Heron Loan<br>Partners</p></div>
    <div class="holder">
      <h1 class="holder-name">Daniel Reyes</h1>
      <p class="holder-role">MANAGING DIRECTOR</p>
      <div class="icon-row">
        <span class="rule"></span>
        <span class="icon" aria-label="Phone">
          <svg width="18" height="18" viewBox="0 0 24 24"><path fill="#fff" d="M6.6 10.8a15 15 0 0 0 6.6 6.6l2.2-2.2c.3-.3.7-.4 1-.2 1.1.4 2.3.6 3.6.6.6 0 1 .4 1 1V20c0 .6-.4 1-1 1A17 17 0 0 1 3 4c0-.6.4-1 1-1h3.5c.6 0 1 .4 1 1 0 1.3.2 2.5.6 3.6.1.3 0 .7-.2 1z"/></svg>
        </span>
        <span class="icon" aria-label="Email">
          <svg width="18" height="18" viewBox="0 0 24 24"><rect x="3" y="6" width="18" height="12" fill="none" stroke="#fff" stroke-width="2"/><path d="M3 6l9 7 9-7" fill="none" stroke="#fff" stroke-width="2"/></svg>
        </span>
        <span class="icon" aria-label="Website">
          <svg width="18" height="18" viewBox="0 0 24 24"><circle cx="12" cy="12" r="8.5" fill="none" stroke="#fff" stroke-width="2"/><path d="M3.5 12h17M12 3.5c3 3 3 14 0 17M12 3.5c-3 3-3 14 0 17" fill="none" stroke="#fff" stroke-width="1.5"/></svg>
        </span>
        <span class="rule"></span>
      </div>
      <ul class="contact-list">
        <li>044-555 010 200</li>
        <li>info@heronloan.com</li>
        <li>www.heronloan.com</li>
      </ul>
      <div class="divider"></div>
      <address class="address">421, Address line goes here<br>45452, Country Name</address>
    </div>
  </article>

  <article class="card card-back">
    <div class="back-pattern" role="img" aria-label="Faint embossed repeating brand pattern on navy"></div>
    <div class="brand"><p class="brand-name">Heron Loan<br>Partners</p></div>
  </article>
</body>
</html>
```